Aquatic View

We need a web design for a new window cleaning company name Tidewell Glass Care. We are located in Grand Cayman, Cayman Islands. We are a small company, a team of husband and wife. Our services include residencial interior and exterior window cleaning and commercial. Extra services such as ceiling fans cleaning, mirrors, high dusting. Home cleaning services. Power washing. Explaining the service. We want a modern, beachy style with aquatic colors. We want to use our domain name "tidewellglasscare.ky". We want to portray a clean, modern and professional design.

Target Market(s)

Big Home owners

Industry/Entity Type

Cleaning Service

Contact Information for Business Card

Company Name: Tidewell Glass Care
Name: Desmond Farrowby owner/manager
Phone: 345-9170452
Email: desmond@tidewellglasscare.ky
Website: tidewellglasscare.ky
Address: P.O.Box 2486 GT, George Town, Grand Cayman KY1-1203 Cayman Islands

Number of Pages Required

2 page

Font styles to use
Sans Serif

Colors
0592cd
0455a3
33a6d7
85cae6
cadf82
abd036
fbf289

Requirements
Nice to have
• Pictures of an ocean view and palm trees from clear windows.
• https://quorvantel.com/bidlinker/
• Use the above for "free estimate".

```html
<!DOCTYPE html>
<html lang="en">
<head>
<meta charset="utf-8">
<title>Tidewell Glass Care</title>
<link href="https://fonts.googleapis.com/css2?family=Roboto:wght@300;400;500&display=swap" rel="stylesheet">
<style>
:root{
  --ocean:#0592cd;
  --navy:#0455a3;
  --sky:#33a6d7;
  --mist:#85cae6;
  --lime-soft:#cadf82;
  --lime:#abd036;
  --white:#ffffff;
  --ink:#3b3b3b;
  --muted:#5d5d4a;
}
*{margin:0;padding:0;box-sizing:border-box}
html,body{width:1200px;height:2446px;overflow:hidden}
body{position:relative;font-family:'Roboto',Arial,sans-serif;background:var(--white);color:var(--ink)}
.abs{position:absolute}

/* header */
.site-header{left:0;top:0;width:1200px;height:78px;background:linear-gradient(#7fc7e8,#3aa3d6 70%,#2f97cc);border-bottom:5px solid var(--white)}
.main-nav a{position:absolute;top:31px;font-size:12.5px;color:var(--white);text-decoration:none;letter-spacing:.3px;font-weight:400}
.brand-tab{left:528px;top:8px;width:144px;height:75px;background:var(--white);border-radius:72px 72px 0 0;display:flex;align-items:center;justify-content:center;text-align:center}
.brand-name{font-size:15px;font-weight:500;color:var(--navy);line-height:1.1;width:110px;margin-top:18px}

/* hero */
.hero{left:0;top:83px;width:1200px;height:471px;background:linear-gradient(165deg,#3f8fe2 0%,#8cc6ef 35%,#27b6d2 55%,#1a9fb4 68%,#2f8a55 82%,#d9c08c 100%)}
.hero-card{left:148px;top:184px;width:305px;height:266px;background:var(--lime)}
.hero-card h1{position:absolute;left:12px;top:36px;font-size:39px;font-weight:300;color:var(--white);line-height:38px;letter-spacing:.3px}
.hero-card .more{position:absolute;left:0;bottom:0;width:100%;height:52px;background:#c4dd6f;color:var(--white);font-size:14px;padding:18px 0 0 27px;letter-spacing:.3px}
.slider-arrow{top:290px;width:22px;height:30px}

/* welcome */
.welcome{left:0;top:554px;width:1200px;height:779px;background:var(--mist)}
.section-title{position:absolute;left:0;width:1200px;text-align:center;color:var(--white);font-weight:400;font-size:39px;letter-spacing:.5px}
.video-frame{left:194px;top:712px;width:810px;height:362px;border:5px solid var(--sky);background:linear-gradient(90deg,#d9c2ad 0%,#f1ece6 35%,#f7f8f8 60%,#e9eef1 100%)}
.play{left:567px;top:855px;width:66px;height:66px}
.welcome-text{left:112px;top:1114px;width:976px;text-align:center;font-size:14.5px;line-height:26px;color:var(--white);font-weight:300}
.quote-btn{left:468px;top:1206px;width:264px;height:61px;background:var(--navy);color:var(--white);font-size:22px;font-weight:300;display:flex;align-items:center;justify-content:center}

/* services */
.services{left:0;top:1333px;width:1200px;height:514px;background:var(--lime-soft)}
.service{position:absolute;top:1470px;width:225px}
.service svg{width:68px;height:68px}
.service h3{position:absolute;left:0;font-size:20px;font-weight:400;color:var(--white);line-height:26px;letter-spacing:.3px}
.service p{position:absolute;left:0;top:220px;font-size:12.5px;line-height:21px;color:var(--muted);font-weight:300;width:222px}

/* testimonials */
.testimonials{left:0;top:1847px;width:1200px;height:404px;background:var(--ocean)}
.client-badge{left:183px;top:1950px;width:244px;height:244px;border-radius:50%;overflow:hidden;display:flex}
.client-photo{width:122px;height:244px;background:linear-gradient(135deg,#6a4a3a,#c9a48a 55%,#3a3d48)}
.client-name{width:122px;height:244px;background:var(--lime);border-left:3px solid var(--ocean);color:var(--white);font-size:21px;line-height:24px;padding:98px 0 0 10px;letter-spacing:.2px}
.quote-mark{left:446px;top:2000px;font-size:40px;color:var(--white);font-family:Georgia,serif}
.quote-text{left:448px;top:2033px;width:600px;font-size:13.5px;line-height:25px;color:var(--white);font-weight:300}
.t-arrow{top:2176px;width:14px;height:20px}

/* footer */
.site-footer{left:0;top:2251px;width:1200px;height:195px;background:var(--white)}
.social{top:2300px;width:31px;height:31px}
.footer-nav{left:0;top:2356px;width:1200px;text-align:center;font-size:12px;color:#444;letter-spacing:.3px}
.footer-nav span.sep{margin:0 17px}
.copyright{left:0;top:2393px;width:1200px;text-align:center;font-size:11.5px;color:#444}
</style>
</head>
<body>

<header class="abs site-header">
  <nav class="main-nav">
    <a style="left:193px">HOME</a>
    <a style="left:279px">ABOUT US</a>
    <a style="left:386px">SERVICES</a>
    <a style="left:708px">FAQ'S</a>
    <a style="left:788px">TESTIMONIALS</a>
    <a style="left:926px">CONTCAT US</a>
  </nav>
</header>
<div class="abs brand-tab"><div class="brand-name">Tidewell Glass Care</div></div>

<section class="abs hero" role="img" aria-label="Tropical beach with turquoise sea, white sand and palm trees"></section>
<div class="abs hero-card">
  <h1>WE DO<br>INTERIOR AND<br>EXTERIOR<br>CLEANING</h1>
  <div class="more">LEARN MORE</div>
</div>
<svg class="abs slider-arrow" style="left:79px" viewBox="0 0 22 30"><path d="M16 3 5 15l11 12" fill="none" stroke="#fff" stroke-width="4"/></svg>
<svg class="abs slider-arrow" style="left:1099px" viewBox="0 0 22 30"><path d="M6 3l11 12L6 27" fill="none" stroke="#fff" stroke-width="4"/></svg>

<section class="abs welcome"></section>
<h2 class="section-title" style="top:638px">WELCOME TO TIDEWELL GLASS CARE</h2>
<div class="abs video-frame" role="img" aria-label="Video still of a smiling cleaner wiping a window with a yellow cloth"></div>
<svg class="abs play" viewBox="0 0 66 66"><circle cx="33" cy="33" r="30" fill="#fff" stroke="#2c9ad3" stroke-width="5"/><path d="M25 19v28l22-14z" fill="#2c9ad3"/></svg>
<p class="abs welcome-text">Sed ut perspiciatis unde omnis iste natus error sit voluptatem accusantium doloremque laudantium, totam rem aperiam, eaque ipsa quae ab illo inventore veritatis et quasi architecto beatae vitae dicta sunt explicabo. Nemo enim ipsam voluptatem quia voluptas sit aspernatur aut odit aut fugit, sed quia consequuntur magni dolores eos qui ratione voluptatem sequi nesciunt. Neque porro quisquam est</p>
<div class="abs quote-btn">GET A FREE QUOTE</div>

<section class="abs services"></section>
<h2 class="section-title" style="top:1380px">OUR SERVICES</h2>

<div class="service" style="left:112px">
  <svg viewBox="0 0 68 68"><rect x="4" y="6" width="56" height="56" fill="none" stroke="#0592cd" stroke-width="5"/><path d="M32 6v56M4 34h56" stroke="#0592cd" stroke-width="5"/><rect x="8" y="38" width="20" height="20" fill="#0592cd"/><rect x="36" y="10" width="20" height="20" fill="#0592cd"/></svg>
  <h3 style="top:130px">INTERIOR AND<br>EXTERIOR WINDOW<br>CLEANING</h3>
  <p>Sed ut perspiciatis unde omnis iste natus error sit voluptatem accusantium doloremque laudantium, totam rem aperiam, eaque ipsa quae</p>
</div>
<div class="service" style="left:361px">
  <svg viewBox="0 0 68 68" fill="none" stroke="#0592cd" stroke-width="5"><ellipse cx="34" cy="17" rx="10" ry="13"/><ellipse cx="34" cy="51" rx="10" ry="13"/><ellipse cx="17" cy="34" rx="13" ry="10"/><ellipse cx="51" cy="34" rx="13" ry="10"/><circle cx="34" cy="34" r="5"/></svg>
  <h3 style="top:130px">CEILING FANS<br>CLEANING</h3>
  <p>Sed ut perspiciatis unde omnis iste natus error sit voluptatem accusantium doloremque laudantium, totam rem aperiam, eaque ipsa quae</p>
</div>
<div class="service" style="left:613px">
  <svg viewBox="0 0 68 68" style="margin-top:-10px;width:84px;height:84px"><path d="M4 4h10v60H4zM54 4h10v60H54z" fill="none" stroke="#0592cd" stroke-width="4"/><path d="M14 10l12 4v40l-12 4M54 10l-12 4v40l12 4" fill="none" stroke="#0592cd" stroke-width="4"/><rect x="26" y="16" width="16" height="36" fill="#0592cd"/></svg>
  <h3 style="top:120px">MIRRORS</h3>
  <p>Sed ut perspiciatis unde omnis iste natus error sit voluptatem accusantium doloremque laudantium, totam rem aperiam, eaque ipsa quae</p>
</div>
<div class="service" style="left:862px">
  <svg viewBox="0 0 68 68" style="margin-top:-12px;width:84px;height:84px"><path d="M62 4 34 32" stroke="#0592cd" stroke-width="5"/><path d="M30 26l12 12-10 10L8 64l2-18z" fill="#0592cd"/><path d="M12 56l10-10M18 60l10-10" stroke="#cadf82" stroke-width="2"/></svg>
  <h3 style="top:120px">HIGH<br>DUSTING</h3>
  <p>Sed ut perspiciatis unde omnis iste natus error sit voluptatem accusantium doloremque laudantium, totam rem aperiam, eaque ipsa quae</p>
</div>

<section class="abs testimonials"></section>
<h2 class="section-title" style="top:1873px">TESTIMONIALS</h2>
<div class="abs client-badge">
  <div class="client-photo" role="img" aria-label="Portrait photo of the client"></div>
  <div class="client-name">CALDER<br>BRENNICK</div>
</div>
<div class="abs quote-mark">&ldquo;</div>
<p class="abs quote-text">But I must explain to you how all this mistaken idea of denouncing pleasure and praising pain was born and I will give you a complete account of the system, and expound the actual teachings of the great explorer of the truth, the master-builder of human happiness. No one rejects, dislikes, or avoids pleasure itself, because it is pleasure,</p>
<svg class="abs t-arrow" style="left:1048px" viewBox="0 0 14 20"><path d="M11 2 3 10l8 8" fill="none" stroke="#fff" stroke-width="2.5"/></svg>
<svg class="abs t-arrow" style="left:1077px" viewBox="0 0 14 20"><path d="M3 2l8 8-8 8" fill="none" stroke="#fff" stroke-width="2.5"/></svg>

<footer class="abs site-footer"></footer>
<span class="abs social" style="left:488px;background:#3b5998"></span>
<span class="abs social" style="left:535px;background:#1d8ac4"></span>
<span class="abs social" style="left:584px;background:#b9b9b9"></span>
<span class="abs social" style="left:632px;background:#1b73a8"></span>
<span class="abs social" style="left:681px;background:#d02a1e"></span>
<div class="abs footer-nav">HOME<span class="sep">|</span>ABOUT US<span class="sep">|</span>SERVICES<span class="sep">|</span>FAQ'S<span class="sep">|</span>TESTIMONIALS<span class="sep">|</span>CONTCAT US</div>
<div class="abs copyright">© 2015 COMPANY NAME | ALL RIGHTS RESERVED</div>

</body>
</html>
```